kolvarin.link kolvarin.space kolvarin.press website

The website is named KOLVARIN and it will have 3 domain names. kolvarin.link, press, space.
I'd like it to be viewed on Pads, pcs and phones.

page menu:

kolvarin.link(start page): presentation of company. (creative, design, app, new product innovation.)
Here we'll need sosial media icons: plimber, vendoloop, mirtavel, trelvanet. (light but some 'fruity' colors)

kolvarin.press: blog. It will be a 75% picture blog > rest will be text. I need to be able to resize pictures and shape columns to picture size. (light but some 'fruity' colors)

kolvarin.space : the fun part of this web design, however, on entering the page I'd like a non-disclosure agreement where viewer simply click "yes, I agree" after filling out contact info. (check attached document)
We will have space here for uploading PDF files viewers can download. There is also a blog space here to tell in brief about the PDF file. (maybe a space/sci-fi theme her e.g spacechimp, Laika the space dog?)

I will attach the logo here I want you to use > and develop for the .space .press webpage. The logo i uploaded is for the .link page.

Target Market(s)

venture capitalists

Number of Pages Required

3 page

Requirements
Must have
• a few 'fruity colors' but mostly white and grey

```html
<!DOCTYPE html>
<html lang="en">
<head>
<meta charset="utf-8">
<title>Kolvarin</title>
<link href="https://fonts.googleapis.com/css2?family=Rajdhani:wght@500;600&family=Lato:wght@400;700&display=swap" rel="stylesheet">
<style>
:root{
  --red:#c85d52;
  --red-band:rgba(200,86,76,.88);
  --blue:#67a5cb;
  --green:#6aac62;
  --purple:#8a55be;
  --ink:#3a3a3a;
  --muted:#555;
  --grey-bg:#ebebeb;
  --page:#f6f6f6;
  --dark:#2e2e2e;
  --darker:#1f1f1f;
  --white:#fff;
}
*{box-sizing:border-box;margin:0;padding:0}
html,body{width:915px;height:1200px;overflow:hidden;background:var(--page);font-family:"Lato",sans-serif;color:var(--ink)}
.page{position:relative;width:915px;height:1200px}
.abs{position:absolute}

.hero{left:0;top:0;width:915px;height:430px;background:linear-gradient(135deg,#c9a27a 0%,#e8e4dc 30%,#f1efe9 55%,#d9cfc2 75%,#8f6e53 100%)}
.topbar{left:0;top:31px;width:915px;height:35px;background:var(--red-band)}
.nav{left:124px;top:31px;height:35px;display:flex;align-items:center;font-family:"Rajdhani",sans-serif;font-weight:500;font-size:12px;color:var(--white)}
.nav a{color:var(--white);text-decoration:none;padding:0 14px;position:relative}
.nav a+a{border-left:1px solid rgba(255,255,255,.35)}
.nav a.active::before,.nav a.active::after{content:"";position:absolute;left:6px;right:6px;height:3px;background:var(--green);border-radius:2px}
.nav a.active::before{top:-11px}.nav a.active::after{bottom:-11px}
.brand{left:381px;top:-36px;width:152px;height:144px;border-radius:50%;background:var(--white);box-shadow:0 3px 8px rgba(0,0,0,.25);display:flex;align-items:flex-end;justify-content:center;padding-bottom:42px;font-family:"Rajdhani",sans-serif;font-weight:600;font-size:21px;letter-spacing:1px;color:var(--dark)}
.contact{top:37px;display:flex;align-items:center;gap:7px;font-family:"Rajdhani",sans-serif;font-weight:500;font-size:12.5px;color:var(--white)}
.contact .ring{width:23px;height:23px;border:1.5px solid var(--white);border-radius:50%;display:flex;align-items:center;justify-content:center}
.caption{left:0;top:368px;width:915px;height:62px;background:rgba(40,40,40,.55)}
.caption h2{position:absolute;left:122px;top:16px;font-family:"Rajdhani",sans-serif;font-weight:500;font-size:23px;color:var(--white)}
.dots{position:absolute;left:757px;top:27px;display:flex;gap:4px}
.dots i{width:9px;height:9px;border-radius:50%;background:var(--white)}
.dots i:first-child{background:var(--red)}

.welcome{left:0;top:460px;width:915px;text-align:center}
.welcome h1{font-family:"Rajdhani",sans-serif;font-weight:500;font-size:20px;color:#555}
.welcome h1 span{color:var(--red)}
.welcome p{width:672px;margin:20px auto 0;font-size:8.8px;line-height:14.7px;color:#444}
.welcome p a{color:var(--green)}

.services{left:0;top:602px;width:915px;height:232px;background:var(--grey-bg);border-top:1px solid #ddd;border-bottom:1px solid #ddd}
.card{top:67px;width:155px;height:113px;color:var(--white);text-align:center}
.card .badge{position:absolute;left:44px;top:-35px;width:68px;height:68px;border-radius:50%;background:var(--white);box-shadow:0 1px 4px rgba(0,0,0,.2);display:flex;align-items:center;justify-content:center}
.card h3{position:absolute;left:0;right:0;top:52px;font-family:"Rajdhani",sans-serif;font-weight:500;font-size:15px;line-height:17px}
.card .plus{position:absolute;left:66px;bottom:-11px;width:23px;height:22px;background:#333;color:var(--white);font-weight:700;font-size:15px;line-height:22px}
.blue{background:var(--blue)}.red{background:var(--red)}.green{background:var(--green)}.purple{background:var(--purple)}

.post{top:894px;width:323px;height:140px;background:var(--white);box-shadow:0 1px 3px rgba(0,0,0,.18)}
.post .photo{position:absolute;left:0;top:0;width:145px;height:140px}
.post h4{position:absolute;left:160px;top:14px;width:110px;font-size:9.5px;line-height:14px;font-weight:700;color:#222}
.post hr{position:absolute;left:157px;top:50px;width:155px;border:0;border-top:1px solid #ddd}
.post p{position:absolute;left:157px;top:60px;width:160px;font-size:9px;line-height:14.5px;color:#444}
.post a{position:absolute;left:158px;top:117px;font-size:7.5px;font-weight:700;color:var(--green);text-decoration:none}
.date{position:absolute;left:268px;top:-20px;width:42px;height:43px;background:var(--green);color:var(--white);text-align:center;border-radius:2px 2px 0 0}
.date b{display:block;font-family:"Rajdhani",sans-serif;font-weight:600;font-size:18px;line-height:24px}
.date small{font-size:8px;font-weight:700}

.footnav{left:0;top:1093px;width:915px;height:41px;background:var(--red);display:flex;align-items:center;justify-content:center;gap:14px;font-size:9.5px;color:var(--white)}
.footnav span.star{font-size:8px;color:#3a2220}
.footnav b{font-weight:400;padding:0 2px}
.footnav b.current{color:#3a2220}
.footinfo{left:0;top:1134px;width:915px;height:38px;background:var(--dark);font-size:9px;color:#ddd}
.footinfo .item{position:absolute;top:0;height:38px;display:flex;align-items:center;gap:6px}
.subscribe{position:absolute;left:609px;top:7px;display:flex;align-items:center;gap:7px}
.subscribe .ring{width:25px;height:25px;border-radius:50%;background:#ddd;display:flex;align-items:center;justify-content:center}
.subscribe .field{width:129px;height:20px;background:#252525;color:#bbb;font-size:7.5px;line-height:20px;padding-left:7px}
.subscribe .go{margin-left:-7px;width:22px;height:20px;background:var(--green);color:var(--white);font-size:9px;font-weight:700;text-align:center;line-height:20px}
.bottombar{left:0;top:1172px;width:915px;height:28px;background:var(--darker);color:var(--white);font-size:8.5px;font-weight:700}
.bottombar .copy{position:absolute;left:124px;top:9px}
.social{position:absolute;right:94px;top:5px;display:flex;gap:8px;font-size:7.5px;font-weight:400}
.social span{display:flex;align-items:center;gap:3px}
.social span::before{content:"";width:9px;height:9px;border-radius:50%;background:var(--white)}
</style>
</head>
<body>
<div class="page">

  <header>
    <div class="abs hero" role="img" aria-label="Photo of a desk notebook sketched with ideas, arrows and a lightbulb, beside glasses and stationery"></div>
    <div class="abs topbar"></div>
    <nav class="abs nav">
      <a class="active" href="#">Home</a>
      <a href="#">About</a>
      <a href="#">Press</a>
      <a href="#">Space</a>
    </nav>
    <div class="abs brand">KOLVARIN</div>
    <div class="abs contact" style="left:555px">
      <span class="ring"><svg width="11" height="9" viewBox="0 0 11 9"><rect x=".6" y=".6" width="9.8" height="7.8" fill="none" stroke="#fff"/><path d="M.6 .8 5.5 5 10.4 .8" fill="none" stroke="#fff"/></svg></span>
      hello@kolvarin.link
    </div>
    <div class="abs contact" style="left:684px">
      <span class="ring"><svg width="10" height="10" viewBox="0 0 10 10"><path d="M2 1l2 2-1 1.2c.6 1.3 1.5 2.2 2.8 2.8L7 6l2 2-1.3 1.3C4.5 9 1 5.5.7 2.3z" fill="#fff"/></svg></span>
      +1 555 0148 372
    </div>
    <div class="abs caption">
      <h2>Share your creativity to world</h2>
      <div class="dots"><i></i><i></i><i></i></div>
    </div>
  </header>

  <section class="abs welcome">
    <h1>Welcome to <span>Brightmere</span></h1>
    <p>Sed ut perspiciatis unde omnis iste natus error sit voluptatem accusantium doloremque laudantium, totam rem aperiam, eaque ipsa quae ab illo inventore veritatis et quasi architecto beatae vitae dicta sunt explicabo. Nemo enim ipsam voluptatem quia voluptas sit aspernatur aut odit aut voluptas sit aspernatur aut odit aut fugit. Sed ut perspiciatis unde omnis iste natus error sit voluptatem accusantium doloremque laudantium, totam rem aperiam, eaque ipsa quae ab illo inventore veritatis et quasi architecto beatae vitae dicta sunt explicabo. Nemo enim ipsam voluptatem quia voluptas sit aspernatur . <a href="#">More</a></p>
  </section>

  <section class="abs services">
    <div class="abs card blue" style="left:122px">
      <div class="badge"><svg width="36" height="36" viewBox="0 0 36 36"><circle cx="18" cy="18" r="15" fill="var(--blue)"/><circle cx="18" cy="18" r="5" fill="none" stroke="#fff" stroke-width="2.5"/><path d="M18 8v4M18 24v4M8 18h4M24 18h4M11 11l3 3M22 22l3 3M25 11l-3 3M14 22l-3 3" stroke="#fff" stroke-width="2.5"/></svg></div>
      <h3>CREATIVE</h3><div class="plus">+</div>
    </div>
    <div class="abs card red" style="left:294px">
      <div class="badge"><svg width="36" height="36" viewBox="0 0 36 36"><g fill="none" stroke="var(--red)" stroke-width="2"><path d="M9 25 24 10l3 3-15 15-4 1z"/><path d="M21 13l3 3"/><path d="M10 9l17 17M8 11l2-2"/></g></svg></div>
      <h3>DESIGN</h3><div class="plus">+</div>
    </div>
    <div class="abs card green" style="left:466px">
      <div class="badge"><svg width="36" height="36" viewBox="0 0 36 36"><g fill="none" stroke="var(--green)" stroke-width="2"><rect x="10" y="5" width="13" height="25" rx="2"/><circle cx="16.5" cy="26.5" r="1"/><circle cx="21" cy="16" r="4"/><path d="M21 9.5v2M21 20.5v2M14.5 16h2M25.5 16h2"/></g></svg></div>
      <h3>APP</h3><div class="plus">+</div>
    </div>
    <div class="abs card purple" style="left:637px">
      <div class="badge"><svg width="36" height="36" viewBox="0 0 36 36"><g fill="none" stroke="var(--purple)" stroke-width="2"><path d="M13 20a7 7 0 1 1 10 0c-1.5 1.5-2 3-2 4h-6c0-1-.5-2.5-2-4z"/><path d="M15 27h6M16 30h4M18 4v3M8 8l2 2M28 8l-2 2M5 17h3M28 17h3"/></g></svg></div>
      <h3>NEW PRODUCT<br>INNOVATION</h3><div class="plus">+</div>
    </div>
  </section>

  <section>
    <article class="abs post" style="left:123px">
      <div class="photo" role="img" aria-label="Illustration of a tree with paint-splash foliage in rainbow colours" style="background:radial-gradient(circle at 55% 38%,#e7683f 0,#c44ba0 22%,#3fa6d8 40%,#f4f4f4 62%)"></div>
      <div class="date"><b>06</b><small>April</small></div>
      <h4>Simply dummy text of the printing</h4>
      <hr>
      <p>Lorem Ipsum is simply dummy text of the printing and typesetting indus text ever since the 1500s,</p>
      <a href="#">Read More &gt;&gt;</a>
    </article>
    <article class="abs post" style="left:469px">
      <div class="photo" role="img" aria-label="Photo of a crumpled yellow paper lightbulb with the word Creative" style="background:radial-gradient(circle at 40% 50%,#f2dc3a 0,#f5f0d0 25%,#f3f3f1 55%)"></div>
      <div class="date"><b>04</b><small>April</small></div>
      <h4>Simply dummy text of the printing</h4>
      <hr>
      <p>Lorem Ipsum is simply dummy text of the printing and typesetting indus text ever since the 1500s,</p>
      <a href="#">Read More &gt;&gt;</a>
    </article>
  </section>

  <footer>
    <nav class="abs footnav">
      <b class="current">HOME</b><span class="star">★</span>
      <b>ABOUT US</b><span class="star">★</span>
      <b>PRESS</b><span class="star">★</span>
      <b>SPACE</b>
    </nav>
    <div class="abs footinfo">
      <div class="item" style="left:128px"><svg width="11" height="15" viewBox="0 0 11 15"><path d="M5.5 0A5.5 5.5 0 0 0 0 5.5C0 9 5.5 15 5.5 15S11 9 11 5.5A5.5 5.5 0 0 0 5.5 0z" fill="#ddd"/><circle cx="5.5" cy="5.5" r="2" fill="var(--dark)"/></svg>Lorem ipsum dolor sit amet, adipiscing elit</div>
      <div class="item" style="left:347px;font-size:10.5px"><svg width="10" height="13" viewBox="0 0 10 10"><path d="M2 1l2 2-1 1.2c.6 1.3 1.5 2.2 2.8 2.8L7 6l2 2-1.3 1.3C4.5 9 1 5.5.7 2.3z" fill="#ddd"/></svg>+1 555 0148 372</div>
      <div class="item" style="left:478px"><span style="font-size:17px">@</span>hello@kolvarin.link</div>
      <div class="subscribe">
        <span class="ring"><svg width="12" height="9" viewBox="0 0 12 9"><rect width="12" height="9" fill="var(--dark)"/><path d="M0 0 6 5 12 0" fill="none" stroke="#ddd"/></svg></span>
        <span class="field">Enter Email</span><span class="go">GO</span>
      </div>
    </div>
    <div class="abs bottombar">
      <span class="copy">Copyright 2016 Kolvarin. All rights reserved.</span>
      <div class="social"><span>mirtavel</span><span>plimber</span><span>vendoloop</span><span>trelvanet</span></div>
    </div>
  </footer>

</div>
</body>
</html>
```